The Velvet Magpie business card

I need a business card for my makeup artist business. I specialise in bridal, glamour, formal and special occasion makeup.
I am a mobile makeup artist who caters for every from nowra to sydney.
I do the following services:
Bridal makeup
airbrush makeup
special occasion
formals
hens nights/ girls night
makeup lesson
makeup for all ages from flower girl to Nanna of the bride!
photoshoot makeup
SPFX

I would like the card to portray a very professional sleek makeup business. I would also like another version of the card directed especially towards brides.

Please see my website to understand colours etc www.thevelvetmagpie-example.com

The Velvet Magpie
Professional Makeup Artist
Lorraine Kedby
0491802643
info@thevelvetmagpie-example.com
www.thevelvetmagpie-example.com
www.facebook.com/thevelvetmagpie

```html
<!DOCTYPE html>
<html lang="en">
<head>
<meta charset="utf-8">
<title>The Velvet Magpie – Business Card</title>
<link rel="stylesheet" href="https://fonts.googleapis.com/css2?family=Oswald:wght@300;400&family=Open+Sans:wght@400;700&display=swap">
<style>
  :root {
    --bg: #eceae7;
    --white: #ffffff;
    --pink: #e0208f;
    --pink-deep: #c8157c;
    --pink-light: #f05bb0;
    --grey: #4a4a4a;
  }
  * { box-sizing: border-box; margin: 0; padding: 0; }
  html, body { width: 1200px; height: 913px; overflow: hidden; background: var(--bg); }
  .canvas { position: relative; width: 1200px; height: 913px; }

  .card {
    position: absolute;
    width: 540px; height: 309px;
    border-radius: 14px;
    overflow: hidden;
    box-shadow: 0 10px 28px rgba(0,0,0,.18);
  }
  .card--front { left: 40px; top: 302px; background: var(--white); }
  .card--back { left: 620px; top: 302px; background: var(--pink); }
  .card svg.card__art { position: absolute; inset: 0; width: 540px; height: 309px; }

  .brand {
    position: absolute; left: 40px; top: 104px;
    font-family: "Oswald", sans-serif; font-weight: 400;
    font-size: 28px; line-height: 40px; letter-spacing: 3px; text-transform: uppercase;
    color: var(--pink); white-space: nowrap;
  }

  .owner { position: absolute; left: 40px; top: 246px; color: var(--white); }
  .owner__name { font-family: "Open Sans", sans-serif; font-weight: 700; font-size: 20px; line-height: 26px; }
  .owner__title { font-family: "Oswald", sans-serif; font-weight: 300; font-size: 15px; line-height: 20px; letter-spacing: .3px; }

  .contacts {
    position: absolute; left: 352px; top: 108px;
    list-style: none; color: var(--white);
    font-family: "Oswald", sans-serif; font-weight: 300; font-size: 12.5px;
  }
  .contacts li { display: flex; align-items: center; gap: 8px; height: 21px; white-space: nowrap; }
  .contacts svg { width: 13px; height: 13px; flex: none; display: block; }

  .services {
    position: absolute; left: 30px; right: 30px; bottom: 22px;
    color: var(--white); text-align: center;
    font-family: "Open Sans", sans-serif; font-weight: 700; font-size: 12.5px; line-height: 1.45;
    text-shadow: 0 1px 2px rgba(120,0,60,.35);
  }
</style>
</head>
<body>
<main class="canvas">

  <section class="card card--front" aria-label="Card front">
    <svg class="card__art" viewBox="0 0 540 309" aria-hidden="true">
      <defs>
        <linearGradient id="pinkFill" x1="0" y1="0" x2="1" y2="1">
          <stop offset="0" stop-color="#ea3ea0"/>
          <stop offset="1" stop-color="#c8157c"/>
        </linearGradient>
      </defs>
      <path class="swoosh-grey" d="M0 214 C120 212 200 200 262 160 C205 208 120 220 0 222 Z" fill="#4a4a4a"/>
      <path class="swoosh-pink" d="M540 16 C420 18 360 70 310 130 C260 195 200 215 0 222 L0 309 L540 309 Z" fill="url(#pinkFill)"/>
      <path class="swoosh-stripe" d="M540 28 C420 30 360 82 310 142 C260 207 200 227 0 234 L0 241 C200 234 264 214 315 149 C365 89 424 38 540 35 Z" fill="#ffffff"/>
    </svg>

    <div class="brand">The Velvet Magpie</div>

    <div class="owner">
      <p class="owner__name">Lorraine Kedby</p>
      <p class="owner__title">Professional Makeup Artist</p>
    </div>

    <ul class="contacts">
      <li>
        <svg viewBox="0 0 16 16" aria-hidden="true"><path fill="#ffffff" d="M4 1.5 6.5 4 5.2 6.2c.9 1.9 2.5 3.5 4.6 4.6L12 9.5l2.5 2.5-1.6 2.3C7.6 14 2 8.4 1.7 3.1Z"/></svg>
        <span>0491802643</span>
      </li>
      <li>
        <svg viewBox="0 0 16 16" aria-hidden="true"><rect x="1" y="3" width="14" height="10" fill="#ffffff"/><path d="M1.5 3.5 8 9l6.5-5.5" fill="none" stroke="#c8157c" stroke-width="1.4"/></svg>
        <span>info@thevelvetmagpie-example.com</span>
      </li>
      <li>
        <svg viewBox="0 0 16 16" aria-hidden="true"><circle cx="8" cy="8" r="7" fill="#ffffff"/><path d="M1 8h14M8 1.2c-2.6 3.8-2.6 9.8 0 13.6M8 1.2c2.6 3.8 2.6 9.8 0 13.6" fill="none" stroke="#c8157c" stroke-width="1"/></svg>
        <span>www.thevelvetmagpie-example.com</span>
      </li>
      <li>
        <svg viewBox="0 0 16 16" aria-hidden="true"><rect x="1.5" y="1.5" width="13" height="13" rx="1.5" fill="#ffffff"/></svg>
        <span>/thevelvetmagpie</span>
      </li>
    </ul>
  </section>

  <section class="card card--back" aria-label="Card back">
    <svg class="card__art" viewBox="0 0 540 309">
      <defs>
        <linearGradient id="backPink" x1="0" y1="0" x2="1" y2="1">
          <stop offset="0" stop-color="#f05bb0"/>
          <stop offset="1" stop-color="#c8157c"/>
        </linearGradient>
        <linearGradient id="photo1" x1="0" y1="0" x2="0" y2="1">
          <stop offset="0" stop-color="#2a2a2a"/><stop offset="1" stop-color="#2f2f6a"/>
        </linearGradient>
        <linearGradient id="photo2" x1="0" y1="0" x2="1" y2="1">
          <stop offset="0" stop-color="#b8b67a"/><stop offset="1" stop-color="#e2c2a8"/>
        </linearGradient>
        <linearGradient id="photo3" x1="0" y1="0" x2="1" y2="1">
          <stop offset="0" stop-color="#e9e4d8"/><stop offset="1" stop-color="#3a3d6e"/>
        </linearGradient>
        <linearGradient id="photo4" x1="0" y1="0" x2="1" y2="0">
          <stop offset="0" stop-color="#9a9088"/><stop offset="1" stop-color="#f0d8c8"/>
        </linearGradient>
      </defs>
      <rect width="540" height="309" fill="url(#backPink)" aria-hidden="true"/>
      <g role="img" aria-label="Photo: two bridesmaids in navy dresses holding a bouquet">
        <polygon points="18,160 140,120 175,240 18,270" fill="url(#photo1)"/>
      </g>
      <g role="img" aria-label="Photo: makeup artist applying mascara to a client">
        <polygon points="140,120 270,76 305,200 175,240" fill="url(#photo2)"/>
      </g>
      <g role="img" aria-label="Photo: two smiling bridesmaids with finished makeup">
        <polygon points="270,76 400,32 430,160 305,200" fill="url(#photo3)"/>
      </g>
      <g role="img" aria-label="Photo: close-up of makeup being applied to a client">
        <polygon points="400,32 522,18 522,122 430,160" fill="url(#photo4)"/>
      </g>
    </svg>
    <p class="services">Bridal makeup • Airbrush makeup • Special occasion • Formals • Hens nights/ Girls night • Makeup lesson • Makeup for all ages from flower girl to Nanna of the bride! • Photoshoot makeup • SPFX</p>
  </section>

</main>
</body>
</html>
```